Global (re)insurance broker needs a business card design

We need a classic business card for our company that is headquartered in SG, with offices in Malaysia and Dubai. We specialise in insurance and reinsurance broking and consultancy for our global clients.

```html
<!DOCTYPE html>
<html lang="en">
<head>
<meta charset="utf-8">
<title>Merivale business card</title>
<link rel="stylesheet" href="https://fonts.googleapis.com/css2?family=Open+Sans:wght@400;600;700&display=swap">
<style>
  :root {
    --brand-blue: #2346a0;
    --brand-green: #bcdcb4;
    --green-deep: #a9d2a0;
    --green-pale: #d8ecd2;
    --ink: #1d1d1f;
    --paper: #f5f5f5;
    --stage: #e4e4e2;
  }
  * { margin: 0; padding: 0; box-sizing: border-box; }
  html, body { width: 1200px; height: 780px; overflow: hidden; }
  body {
    background: var(--stage);
    font-family: "Open Sans", Arial, sans-serif;
    position: relative;
  }
  .card {
    position: absolute;
    top: 236px;
    width: 540px;
    height: 309px;
    border-radius: 3px;
    overflow: hidden;
    box-shadow: 0 6px 18px rgba(0,0,0,.18);
  }
  .card-front { left: 40px; background: var(--paper); }
  .card-back { left: 620px; }

  .brand-name {
    position: absolute;
    top: 38px;
    right: 40px;
    font-size: 64px;
    font-weight: 700;
    letter-spacing: 1px;
    color: var(--brand-blue);
    line-height: 1;
  }
  .holder {
    position: absolute;
    left: 34px;
    top: 138px;
  }
  .holder-name {
    font-size: 30px;
    font-weight: 700;
    line-height: 1.1;
    color: var(--brand-blue);
  }
  .holder-name .surname { color: var(--brand-green); }
  .holder-role {
    font-size: 14px;
    color: var(--ink);
    margin-top: 2px;
  }
  .divider {
    position: absolute;
    left: 222px;
    top: 176px;
    width: 1px;
    height: 70px;
    background: var(--ink);
  }
  .contacts {
    position: absolute;
    left: 240px;
    top: 178px;
    list-style: none;
  }
  .contacts li {
    display: flex;
    align-items: center;
    gap: 10px;
    font-size: 14px;
    color: var(--ink);
    height: 22px;
  }
  .contacts svg { width: 13px; height: 13px; flex: none; }
  .address-band {
    position: absolute;
    left: 0; right: 0; bottom: 0;
    height: 34px;
    background: var(--brand-blue);
    color: #fff;
    font-size: 13.5px;
    display: flex;
    align-items: center;
    padding-left: 34px;
  }

  .back-pattern {
    position: absolute;
    inset: 0;
    background: linear-gradient(110deg, var(--green-deep) 0%, var(--brand-green) 45%, var(--green-pale) 100%);
  }
  .back-brand {
    position: absolute;
    left: 300px;
    top: 196px;
    font-size: 20px;
    font-weight: 700;
    color: #fff;
    letter-spacing: .5px;
  }
</style>
</head>
<body>
  <section class="card card-front">
    <div class="brand-name">MERIVALE</div>
    <div class="holder">
      <div class="holder-name">Clara <span class="surname">Lim</span></div>
      <div class="holder-role">Chief Operating Officer</div>
    </div>
    <div class="divider"></div>
    <ul class="contacts">
      <li>
        <svg viewBox="0 0 14 14" aria-hidden="true"><rect x="3.5" y="1" width="7" height="12" rx="1.2" fill="none" stroke="#9ccb91" stroke-width="1.2"/><line x1="6" y1="11" x2="8" y2="11" stroke="#9ccb91" stroke-width="1"/></svg>
        +65 9123 4560
      </li>
      <li>
        <svg viewBox="0 0 14 14" aria-hidden="true"><circle cx="7" cy="7" r="6" fill="#2346a0"/><path d="M1 7h12M7 1c-2.5 3-2.5 9 0 12M7 1c2.5 3 2.5 9 0 12" stroke="#fff" stroke-width=".8" fill="none"/></svg>
        www.merivale-re.com
      </li>
      <li>
        <svg viewBox="0 0 14 14" aria-hidden="true"><rect x="1" y="3" width="12" height="8.5" rx="1" fill="none" stroke="#9ccb91" stroke-width="1.2"/><path d="M1.5 3.5 7 8l5.5-4.5" fill="none" stroke="#9ccb91" stroke-width="1.2"/></svg>
        clara@merivale-re.com
      </li>
    </ul>
    <div class="address-band">24 Harbour Lane, Meridian Tower #08-04, Singapore 018956</div>
  </section>

  <section class="card card-back">
    <div class="back-pattern" role="img" aria-label="Repeating pattern of the company name set in rows on a soft green background"></div>
    <div class="back-brand">MERIVALE</div>
  </section>
</body>
</html>
```